New Joomla Website for Marquee Hire Co

We need a web design for our new Marquee Hire Co here in New Zealand called Breezy Canopies.
We rather like the retro look, as it fit very well with the current trends in weddings that is a more of a retro look (and we had our logo designed to reflect that!). The 50's and 60's wedding styles are really making a comeback. We would like to communicate to that market effectively.

The Home page should have a slider image with space for a headline on it. It is a visual product we have (but we are selling that dream of a perfect wedding/party/event).

Our competition here have a really nice site that you could look at - www.plovanto.co.nz

The other pages would have space for a picture, and then a blurb under each element related to it.
We will have a FAQ, Gallery, Hire and Contact us pages - we will add them as we go along.

From a technical perspective, we are using Joomla 2.5 and upwards.

Any questions - let me know. I look forward seeing the designs!

Target Market(s)

Couples looking for a wedding marquee, birthday parties, Corporate events

Industry/Entity Type

Wedding

Requirements
Must have
• 1. Preferably done in Joomla. I will also look at Wordpress site.
2. It has to have a retro look and feel.
3. It has to use my brand new logo (included)

```html
<!DOCTYPE html>
<html lang="en">
<head>
<meta charset="utf-8">
<title>Breezy Canopies</title>
<link href="https://fonts.googleapis.com/css2?family=Londrina+Solid:wght@300;400;900&family=Open+Sans:ital,wght@0,400;0,600;1,400&display=swap" rel="stylesheet">
<style>
:root{
  --brown:#4e3420;
  --brown-dark:#3f2a18;
  --cream:#fcf8f2;
  --sand:#f4ece1;
  --sky:#d5e5f0;
  --navy:#34465a;
  --orange:#ef8a2a;
  --rust:#d9552a;
  --text:#4a3a2c;
}
*{box-sizing:border-box;margin:0;padding:0}
html,body{width:985px;height:1200px;overflow:hidden}
body{position:relative;background:var(--cream);font-family:"Open Sans",sans-serif;color:var(--text)}
.abs{position:absolute}
.display{font-family:"Londrina Solid",sans-serif;font-weight:300;letter-spacing:.5px}

.hero-bg{left:0;top:0;width:985px;height:486px;background:linear-gradient(#fff6ec 0%,#fde9d2 60%,#f8cfa5 100%)}
.stripes{left:282px;top:0;width:112px;height:112px;background:linear-gradient(90deg,#c9a493 0 25%,#f3b58f 25% 50%,#f7c79c 50% 75%,#fad6a7 75%)}

.nav{left:61px;top:47px;width:863px;height:52px}
.nav a{position:absolute;top:12px;color:#fbeedd;font-size:22px;text-decoration:none}
.nav .sep{position:absolute;top:16px;width:1px;height:20px;background:#8c6d52}

.badge{left:400px;top:4px;width:166px;height:166px;border-radius:50%;background:#8fb0c8;border:6px solid #f3e6d2;z-index:5}
.brand{left:400px;top:72px;width:166px;text-align:center;color:var(--brown);font-family:"Londrina Solid",sans-serif;font-weight:900;font-size:21px;line-height:24px;z-index:6;white-space:nowrap}

.slider-frame{left:57px;top:111px;width:870px;height:338px;background:#fbf3e8;border-radius:4px}
.slide{left:65px;top:118px;width:854px;height:323px;background:linear-gradient(160deg,#4d6a3a 0%,#e8e6e2 35%,#d9d4cc 55%,#8c7a66 80%,#6d8c94 100%)}
.arrow{top:240px}
.dots{left:464px;top:416px;display:flex;gap:5px}
.dots i{width:10px;height:10px;border-radius:50%;background:#fff;display:block}

.box{top:509px;height:272px;border-radius:4px}
.box h2{position:absolute;left:24px;top:16px;font-size:24px}
.box .rule{position:absolute;left:0;right:0;top:47px;border-top:1px dashed}
.about{left:64px;width:256px;background:var(--brown);color:#f4e8da}
.about h2{color:#fbeedd}
.about .rule{border-color:#8c6d52}
.about .lead{position:absolute;left:25px;top:62px;width:215px;font-size:12px;font-weight:600;line-height:18.5px}
.about .body{position:absolute;left:25px;top:104px;width:225px;font-size:11px;line-height:18.5px;color:#e6d6c4}
.event{left:337px;width:256px;background:var(--sky)}
.event h2{color:var(--navy)}
.event .rule{border-color:#9fb6c8}
.video{left:606px;width:321px;background:var(--sand);border:1px solid #e8dccb}
.video h2{color:var(--brown)}
.video .rule{border-color:#cdb9a0}
.photo{position:absolute;border:3px solid #fff;border-radius:5px;box-shadow:0 1px 3px rgba(0,0,0,.2)}

.section-title{font-size:24px;color:var(--brown)}
.quote{font-family:Georgia,serif;font-size:34px;color:var(--brown);font-weight:700;line-height:1}
.avatar{width:71px;height:64px;border:3px solid #fff;box-shadow:0 1px 3px rgba(0,0,0,.25);background:linear-gradient(#d9c2a8,#b08a6a)}
.tq{font-size:9.5px;font-style:italic;line-height:17px;color:#5a4535;white-space:nowrap}
.author{font-size:12px;color:#4a3a2c}

.faq{left:636px;top:856px;width:241px;list-style:none}
.faq li{font-size:12px;padding:6px 0 8px;border-bottom:1px solid #ece2d6;white-space:nowrap}
.faq li:last-child{border-bottom:0}

.footer{left:0;top:1071px;width:985px;height:129px;background:var(--brown-dark)}
.foot-links{left:71px;top:1117px;font-size:12px;color:#f4e8da;word-spacing:2px}
.copy{left:71px;top:1146px;font-size:10.5px;color:#e4d4c2}
.social{top:1116px;width:30px;height:30px;border-radius:50%;background:#f4ece1}
</style>
</head>
<body>

<div class="abs hero-bg"></div>
<div class="abs stripes"></div>
<svg class="abs" style="left:0;top:380px" width="985" height="106" viewBox="0 0 985 106">
  <polygon points="0,60 120,40 60,106 0,106" fill="#a33d22"/>
  <polygon points="60,106 160,30 360,30 330,106" fill="var(--rust)"/>
  <polygon points="330,106 360,30 560,30 790,106" fill="var(--orange)"/>
  <polygon points="560,30 985,30 985,106 790,106" fill="#f8c98f"/>
</svg>

<svg class="abs nav" viewBox="0 0 863 52" width="863" height="52">
  <polygon points="0,0 863,0 844,26 863,52 0,52 19,26" fill="var(--brown)"/>
</svg>
<nav class="abs nav display">
  <a style="left:53px">HOME</a><span class="sep" style="left:115px"></span>
  <a style="left:140px">FAQ</a><span class="sep" style="left:197px"></span>
  <a style="left:221px">GALLERY</a>
  <a style="left:601px">HIRE</a><span class="sep" style="left:657px"></span>
  <a style="left:680px">CONTACT US</a>
</nav>

<div class="abs slider-frame"></div>
<div class="abs slide" role="img" aria-label="Guests mingling outside a white stretch marquee in a garden"></div>
<svg class="abs" style="left:65px;top:380px" width="854" height="61" viewBox="0 0 854 61">
  <path d="M0,61 L0,55 Q430,45 854,5 L854,61 Z" fill="#3e2e24"/>
  <path d="M0,55 Q430,45 854,5" stroke="var(--orange)" stroke-width="4" fill="none"/>
</svg>
<svg class="abs arrow" style="left:82px" width="20" height="56" viewBox="0 0 20 56"><polyline points="18,2 3,28 18,54" fill="none" stroke="#fff" stroke-width="3"/></svg>
<svg class="abs arrow" style="left:882px" width="20" height="56" viewBox="0 0 20 56"><polyline points="2,2 17,28 2,54" fill="none" stroke="#fff" stroke-width="3"/></svg>
<div class="abs dots"><i></i><i></i><i></i><i></i></div>

<div class="abs badge"></div>
<div class="abs brand">Breezy Canopies</div>

<section class="abs box about">
  <h2 class="display">ABOUT US</h2><div class="rule"></div>
  <p class="lead">Duis tincidunt lectus quis dui viverra vestibulum.vulputate aliquam dui.</p>
  <p class="body">Nunc tempus felis vitae urna. Vivamus porttitor, g, purus nisi eleifend libero, a tempus libero lectus feugiat felis. Morbi diam mauris, viverra in, gravida eu, mattis in, ante. Morbi eget arcu. Morbi porta, libero id ullamcorper nonummy, nibh ligula pulvinar metus</p>
</section>

<section class="abs box event">
  <h2 class="display">LATEST EVENT</h2><div class="rule"></div>
  <div class="photo" role="img" aria-label="Cheering crowd waving red flags" style="left:14px;top:61px;width:229px;height:121px;background:linear-gradient(135deg,#6b6f6a,#c23a2e 45%,#3f7a4a 75%,#d9c9b0)"></div>
  <div class="photo" role="img" aria-label="Table with glassware" style="left:15px;top:191px;width:70px;height:63px;background:linear-gradient(#3e5f8a,#d8c7a0)"></div>
  <div class="photo" role="img" aria-label="Conference room with microphones" style="left:94px;top:191px;width:70px;height:63px;background:linear-gradient(#8a5a48,#e8e4de)"></div>
  <div class="photo" role="img" aria-label="Fans celebrating at a stadium" style="left:172px;top:191px;width:70px;height:63px;background:linear-gradient(#d85a3a,#e8c23a)"></div>
</section>

<section class="abs box video">
  <h2 class="display">WATCH OUR VIDEO</h2><div class="rule"></div>
  <div class="photo" role="img" aria-label="Video still of friends toasting in a bar" style="left:14px;top:56px;width:292px;height:200px;background:linear-gradient(100deg,#4d6ea0 0%,#8a6a50 40%,#c89a78 65%,#5a3a5a 100%)"></div>
  <svg class="abs" style="left:140px;top:137px" width="40" height="40" viewBox="0 0 40 40"><circle cx="20" cy="20" r="18" fill="#1d1a18" stroke="#fff" stroke-width="2"/><polygon points="16,12 28,20 16,28" fill="#fff"/></svg>
</section>

<h2 class="abs display section-title" style="left:63px;top:820px">CUSTOMER TESTIMONIALS</h2>

<div class="abs quote" style="left:62px;top:860px">“</div>
<div class="abs avatar" role="img" aria-label="Customer portrait" style="left:87px;top:859px"></div>
<p class="abs tq" style="left:169px;top:852px">Nunc tempus felis vitae urna. Vi-<br>vamus porttitor, neque at volut-<br>pat rutrum, purus nisi eleifend<br>libero, a tempus libero lectus</p>
<p class="abs tq" style="left:84px;top:924px">Morbi eget arcu. Morbi porta, libero id ullamcorper<br>nonummy, nibh ligula pulvinar metus, eget consect-<br>etuer augue nisi quis lacus. Ut ac mi quis lacus.</p>
<p class="abs author" style="left:85px;top:987px">By Author Name</p>

<div class="abs quote" style="left:346px;top:860px">“</div>
<div class="abs avatar" role="img" aria-label="Customer portrait" style="left:371px;top:859px"></div>
<p class="abs tq" style="left:453px;top:852px">Nunc tempus felis vitae urna. Vi-<br>vamus porttitor, neque at volut-<br>pat rutrum, purus nisi eleifend<br>libero, a tempus libero lectus</p>
<p class="abs tq" style="left:368px;top:924px">Morbi eget arcu. Morbi porta, libero id ullamcorper<br>nonummy, nibh ligula pulvinar metus, eget consect-<br>etuer augue nisi quis lacus. Ut ac mi quis lacus.</p>
<p class="abs author" style="left:369px;top:987px">By Author Name</p>

<h2 class="abs display section-title" style="left:636px;top:820px">RECENT FAQ'S</h2>
<ul class="abs faq">
  <li>Phasellus felis dolor, scelerisque  tempus</li>
  <li>Eget lobortis id libero.</li>
  <li>Donec scelerisque leo ac risus.</li>
  <li>Praesent sit amet est in dictum dolor eu dictum</li>
  <li>Duis sed tellus et tortor vestibulum gravida</li>
</ul>

<svg class="abs" style="left:0;top:1063px" width="985" height="10" viewBox="0 0 985 10" preserveAspectRatio="none">
  <path d="M0,10 L0,0 l8,8 l8,-8 l8,8 l8,-8 l8,8 l8,-8 l8,8 l8,-8 l8,8 l8,-8 l8,8 l8,-8 l8,8 l8,-8 l8,8 l8,-8 l8,8 l8,-8 l8,8 l8,-8 l8,8 l8,-8 l8,8 l8,-8 l8,8 l8,-8 l8,8 l8,-8 l8,8 l8,-8 l8,8 l8,-8 l8,8 l8,-8 l8,8 l8,-8 l8,8 l8,-8 l8,8 l8,-8 l8,8 l8,-8 l8,8 l8,-8 l8,8 l8,-8 l8,8 l8,-8 l8,8 l8,-8 l8,8 l8,-8 l8,8 l8,-8 l8,8 l8,-8 l8,8 l8,-8 l8,8 l8,-8 l8,8 l8,-8 l8,8 l8,-8 l8,8 l8,-8 l8,8 l8,-8 l8,8 l8,-8 l8,8 l8,-8 l8,8 l8,-8 l8,8 l8,-8 l8,8 l8,-8 l8,8 l8,-8 l8,8 l8,-8 l8,8 l8,-8 l8,8 l8,-8 l8,8 l8,-8 l8,8 l8,-8 l8,8 l8,-8 l8,8 l8,-8 l8,8 l8,-8 l8,8 l8,-8 l8,8 l8,-8 l8,8 l8,-8 l8,8 l8,-8 l8,8 l8,-8 l8,8 l8,-8 l8,8 l8,-8 l8,8 l8,-8 l8,8 l8,-8 l8,8 l8,-8 l8,8 l8,-8 l8,8 l8,-8 l8,8 l8,-8 l8,8 l8,-8 l8,8 l8,-8 l8,8 l8,-8 L985,0 L985,10 Z" fill="var(--brown-dark)"/>
</svg>
<footer class="abs footer"></footer>
<p class="abs foot-links">Home &nbsp;|&nbsp; FAQ &nbsp;|&nbsp; Gallery &nbsp;|&nbsp; Hire &nbsp;|&nbsp; Contact us</p>
<p class="abs copy">Copyright © 2013 Company Name.  All right reserved.</p>
<span class="abs social" style="left:779px"></span>
<span class="abs social" style="left:812px"></span>
<span class="abs social" style="left:846px"></span>
<span class="abs social" style="left:879px"></span>

</body>
</html>
```